FernPath....... a dash of Glow

I need a web design for a new business based in London that will be mobile (offered at homes, parks or a local cafe ect) called FernPath. I offer Life Coaching/Counselling sessions, Personal training, Massage and Sports Massage. Sessions range from an hour to half and hour. My aim is to help people along their journey to help give them gain clarity of where there going, helping them to towards their goals, so that can experience bliss. My website should represent a place people can come to release their stress and worries so that they leave feeling lighter, clearer and happier. I would like my website to reflect someone feeling ALIVE. I would also like a logo design for FernPath with a sentence underneath or near saying A dash of Glow.

Target Market(s)

middle class people

Industry/Entity Type

Business

Coding

Coded - Design and coding required

Number of Pages Required

4 page

Requirements
Must have
• 1st page About us
• 2nd page Services
• 3rd page Prices
• 4th page contact details
Nice to have
• mixture of cultures in images

```html
<!DOCTYPE html>
<html lang="en">
<head>
<meta charset="utf-8">
<title>FernPath – A dash of Glow</title>
<link href="https://fonts.googleapis.com/css2?family=Lato:wght@400;700;900&family=PT+Sans:ital,wght@0,400;0,700;1,400&display=swap" rel="stylesheet">
<style>
:root{
  --orange:#f26a3f;
  --yellow:#f2be2e;
  --olive:#6b5a16;
  --olive-soft:#9c8a4a;
  --ink:#444;
  --muted:#8a8a8a;
  --rose:#e9506a;
  --gold-a:#f5cf3c;
  --gold-b:#d9a410;
  --footer:#1f1f1f;
  --topline:#4a0c12;
}
*{margin:0;padding:0;box-sizing:border-box}
html,body{width:762px;height:1200px;overflow:hidden;background:#fff}
body{position:relative;font-family:"PT Sans",sans-serif;color:var(--ink)}
.abs{position:absolute}

/* header */
.topline{left:0;top:0;width:762px;height:3px;background:var(--topline)}
.brand{left:40px;top:18px;width:120px;text-align:center}
.brand-dot{display:block;margin:0 auto 4px;width:20px;height:20px;border-radius:50%;background:var(--orange);opacity:.85}
.brand-name{font-family:"Lato",sans-serif;font-size:18px;color:var(--olive);line-height:1}
.brand-tag{font-size:8.5px;color:var(--olive-soft);letter-spacing:.5px;margin-top:3px}
.login{left:630px;top:12px;width:69px;height:21px;background:linear-gradient(var(--gold-a),var(--gold-b));color:#fff;font-size:9px;display:flex;align-items:center;justify-content:center;gap:5px}
.nav{left:318px;top:46px;display:flex;font-size:9px;color:#555}
.nav a{color:inherit;text-decoration:none;position:relative}
.nav a.active{color:var(--rose)}
.nav a.active::after{content:"";position:absolute;left:-2px;right:-2px;top:16px;height:2px;background:var(--rose)}
.search{left:688px;top:48px}

/* hero */
.hero{left:0;top:84px;width:762px;height:304px;background:radial-gradient(ellipse at 60% 35%,#f7d77a 0%,#e3a52a 30%,#b86a10 65%,#6e3a06 100%)}
.hero-shadow{left:30px;top:386px;width:702px;height:10px;border-radius:50%;box-shadow:0 6px 8px -4px rgba(0,0,0,.25)}
.hero-title{left:60px;top:196px;font-family:"Lato",sans-serif;font-weight:900;font-size:46px;color:#fff;text-shadow:0 2px 4px rgba(0,0,0,.35);letter-spacing:1px}
.hero-sub{left:74px;top:250px;font-family:"Lato",sans-serif;font-size:16px;color:#fff;letter-spacing:8px}
.chev{top:222px}

/* section headings */
.heading{width:762px;left:0;text-align:center;font-family:"Lato",sans-serif;font-size:22px;font-weight:400;color:var(--orange)}
.heading .y{color:var(--yellow)}
.lead{width:762px;left:0;text-align:center;font-size:7.5px;font-style:italic;color:var(--muted)}

/* services */
.service{width:160px;text-align:center}
.service-ring{margin:0 auto;width:68px;height:68px;border-radius:50%;border:1.5px solid var(--orange);border-right-color:var(--yellow);border-bottom-color:var(--yellow);display:flex;align-items:center;justify-content:center}
.service-title{margin-top:6px;font-size:11px;color:var(--orange)}
.service-title .y{color:var(--yellow)}
.service-text{margin-top:3px;font-size:7px;line-height:13px;color:var(--muted)}

/* about */
.about{left:0;top:651px;width:762px;height:203px;background:linear-gradient(100deg,#8a6a5e 0%,#a88676 35%,#c9aa98 60%,#ead8ca 100%)}
.about-veil{left:0;top:651px;width:762px;height:203px;background:rgba(60,50,60,.35)}
.about-title{left:0;width:762px;top:684px;text-align:center;font-family:"Lato",sans-serif;font-size:21px;font-weight:400;color:#fff}
.about-text{left:118px;width:526px;top:717px;text-align:center;font-size:7.4px;line-height:14.8px;color:#f4f0ee}
.btn-read{left:338px;top:786px;width:87px;height:20px;background:linear-gradient(var(--gold-a),var(--gold-b));color:#fff;font-size:8px;display:flex;align-items:center;justify-content:center}

/* events */
.event{width:200px}
.event.left{text-align:right}
.event-title{font-size:11px;color:#555}
.event-meta{font-size:8px;color:#9a9a9a;margin-top:7px;display:flex;align-items:center;gap:6px}
.event.left .event-meta{justify-content:flex-end}
.date{width:48px;height:48px;border-radius:50%;border:1.5px solid var(--orange);border-right-color:var(--yellow);border-bottom-color:var(--yellow);text-align:center;color:#444}
.date .d{font-size:8px;margin-top:9px}
.date .m{font-size:10px;font-weight:700;margin-top:2px}
.center-brand{left:301px;top:986px;width:160px;text-align:center}
.center-brand .brand-dot{width:14px;height:14px;margin-bottom:8px}
.center-brand .brand-name{font-size:21px}
.center-brand .brand-tag{font-size:10.5px;letter-spacing:.5px;margin-top:4px}

/* footer */
.footer{left:0;top:1130px;width:762px;height:70px;background:var(--footer)}
.foot-links{left:0;width:762px;top:1152px;text-align:center;font-size:8px;color:#ddd;word-spacing:2px}
.foot-copy{left:0;width:762px;top:1169px;text-align:center;font-size:7.5px;color:#ddd}
.social{left:606px;top:1156px;display:flex;gap:3px}
.social-link{width:16px;height:16px;border-radius:50%;border:1.2px solid #ddd;display:flex;align-items:center;justify-content:center}
.social-link::after{content:"";width:5px;height:5px;border-radius:50%;background:#ddd}
</style>
</head>
<body>

<header>
  <div class="abs topline"></div>
  <div class="abs brand">
    <span class="brand-dot"></span>
    <div class="brand-name">Fern Path</div>
    <div class="brand-tag">A dash of Glow</div>
  </div>
  <div class="abs login">
    <svg width="8" height="8" viewBox="0 0 10 10"><path d="M1 4h4V2l3 3-3 3V6H1z" fill="#fff"/><path d="M6 1h3v8H6" fill="none" stroke="#fff" stroke-width="1.2"/></svg>
    Log In
  </div>
  <nav class="abs nav">
    <a class="active" href="#">Home</a>
    <a href="#" style="margin-left:26px">About Us</a>
    <a href="#" style="margin-left:29px">Services</a>
    <a href="#" style="margin-left:27px">Our Aim</a>
    <a href="#" style="margin-left:29px">Testimonials</a>
    <a href="#" style="margin-left:30px">Contacts</a>
  </nav>
  <svg class="abs search" width="9" height="9" viewBox="0 0 10 10"><circle cx="4" cy="4" r="3" fill="none" stroke="var(--rose)" stroke-width="1.6"/><path d="M6.2 6.2L9 9" stroke="var(--rose)" stroke-width="1.8"/></svg>
</header>

<section>
  <div class="abs hero" role="img" aria-label="Joyful woman with arms open in a sunlit golden meadow"></div>
  <div class="abs hero-shadow"></div>
  <div class="abs hero-title">FERNPATH</div>
  <div class="abs hero-sub">A dash of Glow</div>
  <svg class="abs chev" style="left:24px" width="14" height="26" viewBox="0 0 14 26"><path d="M12 1L2 13l10 12" fill="none" stroke="#fff" stroke-width="1.2" opacity=".8"/></svg>
  <svg class="abs chev" style="left:722px" width="14" height="26" viewBox="0 0 14 26"><path d="M2 1l10 12L2 25" fill="none" stroke="#fff" stroke-width="1.2" opacity=".8"/></svg>
</section>

<section>
  <h1 class="abs heading" style="top:412px">Welcome to F<span class="y">ernPath</span></h1>
  <p class="abs lead" style="top:445px">Nemo enim ipsam voluptatem quia voluptas sit aspernatur aut odit aut fugit, sed quia consequuntur</p>

  <svg class="abs" style="left:62px;top:518px" width="14" height="36" viewBox="0 0 14 36"><path d="M12 1L2 18l10 17" fill="none" stroke="#ddd" stroke-width="1"/></svg>
  <svg class="abs" style="left:686px;top:518px" width="14" height="36" viewBox="0 0 14 36"><path d="M2 1l10 17L2 35" fill="none" stroke="#ddd" stroke-width="1"/></svg>

  <div class="abs service" style="left:114px;top:485px">
    <div class="service-ring">
      <svg width="32" height="28" viewBox="0 0 32 28" fill="none" stroke="var(--orange)" stroke-width="1.4" stroke-linejoin="round"><path d="M3 3h26v16H14l-6 6v-6H3z"/><path d="M9 10h14M9 14h9"/></svg>
    </div>
    <div class="service-title">Life Co<span class="y">aching</span></div>
    <div class="service-text">Nemo enim ipsam voluptatem quia sit<br>aspernatur aut odit aut fugit, sed quia magni<br>dolores eos qui ratione voluptatem</div>
  </div>

  <div class="abs service" style="left:301px;top:485px">
    <div class="service-ring">
      <svg width="34" height="18" viewBox="0 0 34 18" fill="none" stroke="var(--orange)" stroke-width="1.4" stroke-linejoin="round"><rect x="4" y="2" width="5" height="14" rx="1"/><rect x="25" y="2" width="5" height="14" rx="1"/><path d="M1 6v6M33 6v6M9 9h16"/></svg>
    </div>
    <div class="service-title">Person<span class="y">al training</span></div>
    <div class="service-text">Nemo enim ipsam voluptatem quia sit<br>aspernatur aut odit aut fugit, sed quia magni<br>dolores eos qui ratione voluptatem</div>
  </div>

  <div class="abs service" style="left:496px;top:485px">
    <div class="service-ring">
      <svg width="34" height="34" viewBox="0 0 34 34" fill="none" stroke="var(--yellow)" stroke-width="1.4"><ellipse cx="17" cy="6" rx="4" ry="2.5"/><ellipse cx="17" cy="13" rx="7" ry="3"/><ellipse cx="17" cy="21" rx="10" ry="3.5"/><ellipse cx="17" cy="29" rx="13" ry="3.5"/></svg>
    </div>
    <div class="service-title">Massage and Sp<span class="y">orts Massage</span></div>
    <div class="service-text">Nemo enim ipsam voluptatem quia sit<br>aspernatur aut odit aut fugit, sed quia<br>magni dolores eos ...</div>
  </div>
</section>

<section>
  <div class="abs about" role="img" aria-label="Relaxing facial massage being given with gentle hands"></div>
  <div class="abs about-veil"></div>
  <h2 class="abs about-title">About Us</h2>
  <p class="abs about-text">ut perspiciatis unde omnis iste natus error sit voluptatem accusantium doloremque laudantium, totam rem aperiam, eaque ipsa quae ab illo inventore veritatis et quasi architecto beatae vitae dicconsequuntur magni dolores eos qui ratioula dolor sit amet, consectetam quaerat voluptatem. Ut enim ad minima veniam, quis nostrum exercitationem ullam corporis suscipit laboriosam, nisi ut aliquid ex ea commodi consequatur? Quis autem vel eum iure reprehenderit qui in ea voluptate velit esse quam nihil molestiae consequatur, vel illum qui dolorem eum</p>
  <div class="abs btn-read">Read More &gt;&gt;</div>
</section>

<section>
  <h2 class="abs heading" style="top:879px">Latest <span class="y">Events</span></h2>
  <p class="abs lead" style="top:912px">Nemo enim ipsam voluptatem quia voluptas sit aspernatur aut odit aut fugit, sed quia consequuntur</p>

  <div class="abs event left" style="left:18px;top:964px">
    <div class="event-title">Life Coaching/Counselling</div>
    <div class="event-meta">8.00 am - 5.00 <svg width="8" height="8" viewBox="0 0 10 10"><circle cx="5" cy="5" r="4" fill="none" stroke="var(--rose)" stroke-width="1.3"/><path d="M5 3v2h2" stroke="var(--rose)" fill="none"/></svg></div>
    <div class="event-meta">Street Name, City Name <svg width="7" height="9" viewBox="0 0 8 10"><path d="M4 10S0 5.5 0 4a4 4 0 018 0c0 1.5-4 6-4 6z" fill="var(--rose)"/><circle cx="4" cy="4" r="1.4" fill="#fff"/></svg></div>
  </div>
  <div class="abs date" style="left:238px;top:962px"><div class="d">02</div><div class="m">DEC</div></div>

  <div class="abs event left" style="left:18px;top:1052px">
    <div class="event-title">Personal training</div>
    <div class="event-meta">8.00 am - 5.00 <svg width="8" height="8" viewBox="0 0 10 10"><circle cx="5" cy="5" r="4" fill="none" stroke="var(--rose)" stroke-width="1.3"/><path d="M5 3v2h2" stroke="var(--rose)" fill="none"/></svg></div>
    <div class="event-meta">Street Name, City Name <svg width="7" height="9" viewBox="0 0 8 10"><path d="M4 10S0 5.5 0 4a4 4 0 018 0c0 1.5-4 6-4 6z" fill="var(--rose)"/><circle cx="4" cy="4" r="1.4" fill="#fff"/></svg></div>
  </div>
  <div class="abs date" style="left:238px;top:1050px"><div class="d">02</div><div class="m">DEC</div></div>

  <div class="abs center-brand">
    <span class="brand-dot"></span>
    <div class="brand-name">Fern Path</div>
    <div class="brand-tag">A dash of Glow</div>
  </div>

  <div class="abs date" style="left:475px;top:962px"><div class="d">02</div><div class="m">DEC</div></div>
  <div class="abs event" style="left:541px;top:964px">
    <div class="event-title">Massage and Sports Massage</div>
    <div class="event-meta"><svg width="8" height="8" viewBox="0 0 10 10"><circle cx="5" cy="5" r="4" fill="none" stroke="var(--rose)" stroke-width="1.3"/><path d="M5 3v2h2" stroke="var(--rose)" fill="none"/></svg> December 02 @ 8.00 am - 5.00</div>
    <div class="event-meta"><svg width="7" height="9" viewBox="0 0 8 10"><path d="M4 10S0 5.5 0 4a4 4 0 018 0c0 1.5-4 6-4 6z" fill="var(--rose)"/><circle cx="4" cy="4" r="1.4" fill="#fff"/></svg> Street Name, City Name</div>
  </div>

  <div class="abs date" style="left:475px;top:1050px"><div class="d">02</div><div class="m">DEC</div></div>
  <div class="abs event" style="left:541px;top:1052px">
    <div class="event-title">Life Coaching/Counselling</div>
    <div class="event-meta"><svg width="8" height="8" viewBox="0 0 10 10"><circle cx="5" cy="5" r="4" fill="none" stroke="var(--rose)" stroke-width="1.3"/><path d="M5 3v2h2" stroke="var(--rose)" fill="none"/></svg> December 02 @ 8.00 am - 5.00</div>
    <div class="event-meta"><svg width="7" height="9" viewBox="0 0 8 10"><path d="M4 10S0 5.5 0 4a4 4 0 018 0c0 1.5-4 6-4 6z" fill="var(--rose)"/><circle cx="4" cy="4" r="1.4" fill="#fff"/></svg> Street Name, City Name</div>
  </div>
</section>

<footer>
  <div class="abs footer"></div>
  <div class="abs foot-links">Home &nbsp;| &nbsp;About Us &nbsp;| &nbsp;Services &nbsp;| &nbsp;Our Aim &nbsp;| &nbsp;Testimonials &nbsp;| &nbsp;Contacts</div>
  <div class="abs foot-copy">© 2015. FernPath.com All rights reserved</div>
  <div class="abs social" aria-label="Social links">
    <span class="social-link"></span><span class="social-link"></span><span class="social-link"></span><span class="social-link"></span><span class="social-link"></span>
  </div>
</footer>

</body>
</html>
```